We are a local Communty Pharmacy wishing to promote and market a specialised Pharmaceutical Service

We would like a design that is professional and enticing ( according to the brief In attached files)
We wish to Market Harbourside Pharmacy as a specialist side of our business.
We have the expertise a purpose built preparation laboratory.
The main purpose is an Internet presence that entices prospective patients to contact or visit our physical store.

Target Market(s)

Patients Medicos and Veterinary clients

Industry/Entity Type

Pharmacy

Coding

Coded - Design and coding required

Number of Pages Required

1 page

Requirements
Must have
• Clear friendly image
Nice to have
• soft enticing feel
Should not have
• No crass loud unprofessional elements

```html
<!DOCTYPE html>
<html lang="en">
<head>
<meta charset="utf-8">
<title>Harbourside Pharmacy</title>
<link rel="stylesheet" href="https://fonts.googleapis.com/css2?family=Raleway:wght@400;500;600;700&family=Open+Sans:wght@400;600&display=swap">
<style>
:root{
  --blue:#27a4dc;
  --blue-dark:#1a8fc6;
  --blue-light:#5fc1ea;
  --blue-pale:#e8f5fc;
  --ink:#3a3f44;
  --muted:#8a9096;
  --line:#dfe3e6;
  --bar:#3b3f43;
  --footer:#2f3236;
  --white:#ffffff;
}
*{box-sizing:border-box;margin:0;padding:0}
html,body{width:1200px;height:2364px;overflow:hidden}
body{position:relative;background:var(--white);font-family:'Open Sans',sans-serif;color:var(--ink)}
.topbar{position:absolute;left:0;top:0;width:1200px;height:32px;background:var(--bar);color:#cfd3d6;font-size:12px;display:flex;align-items:center;justify-content:space-between;padding:0 40px 0 44px}
.social{display:flex;gap:10px}
.social span{width:20px;height:20px;border-radius:50%;background:#5a5f64;display:block}
.header{position:absolute;top:32px;left:0;width:1200px;height:80px;display:flex;align-items:center;justify-content:space-between;padding:0 44px;border-bottom:1px solid var(--line)}
.brand{font-family:'Raleway',sans-serif;font-size:26px;font-weight:500;color:var(--ink)}
.nav{display:flex;gap:6px;font-family:'Raleway',sans-serif;font-size:15px}
.nav a{padding:8px 14px;color:var(--ink);text-decoration:none}
.nav a.active{background:var(--blue);color:var(--white)}
.hero{position:absolute;top:112px;left:0;width:1200px;height:480px;background:linear-gradient(110deg,#d9e6ee 0%,#eef4f8 45%,#c9dce8 100%)}
.hero-photo{position:absolute;inset:0;background:radial-gradient(circle at 75% 40%,#f4f7f9 0%,rgba(244,247,249,0) 40%),linear-gradient(160deg,#cfe0ea,#e6eff4 60%,#b9d1e0)}
.hero-text{position:absolute;left:112px;top:150px;width:460px}
.hero-text h1{font-family:'Raleway',sans-serif;font-size:30px;font-weight:600;color:var(--ink);letter-spacing:.5px}
.hero-text p{margin-top:18px;font-size:13px;line-height:20px;color:#4f5559}
.btn{display:inline-block;margin-top:34px;background:var(--bar);color:var(--white);font-size:12px;padding:10px 18px;font-family:'Raleway',sans-serif}
.features{position:absolute;top:592px;left:208px;width:896px;height:240px;display:flex}
.feature{flex:1;background:var(--blue);color:var(--white);display:flex;flex-direction:column;align-items:center;padding-top:30px;font-family:'Raleway',sans-serif;font-size:19px;font-weight:500}
.feature.mid{background:var(--blue-light)}
.feature svg{height:78px;width:78px}
.feature .label{margin-top:22px}
.feature .plus{margin-top:20px;width:30px;height:30px;background:var(--white);color:var(--blue);display:flex;align-items:center;justify-content:center;font-size:22px;font-weight:700;line-height:1}
.section-title{position:absolute;left:0;width:1200px;display:flex;align-items:center;justify-content:center;gap:20px;font-family:'Raleway',sans-serif;font-size:24px;font-weight:600;color:var(--blue)}
.section-title .rule{width:150px;height:1px;background:var(--line)}
.section-title .dot{width:22px;height:22px;border:2px solid var(--blue);display:block;position:relative}
.section-title .dot::after{content:"";position:absolute;inset:5px;background:var(--blue)}
.info{position:absolute;top:1010px;left:112px;width:980px;display:grid;grid-template-columns:1fr 1fr;column-gap:60px;row-gap:66px}
.info-item{display:flex;gap:20px;border-bottom:1px solid var(--line);padding-bottom:18px}
.info-icon{flex:none;width:56px;height:56px;background:var(--blue);display:flex;align-items:center;justify-content:center}
.info-item h3{font-family:'Raleway',sans-serif;font-size:18px;font-weight:600;margin-bottom:10px}
.info-item p{font-size:11px;line-height:18px;color:var(--muted)}
.products{position:absolute;top:1488px;left:88px;width:1024px;display:flex;gap:32px}
.product{width:232px}
.product-img{height:220px;border:1px solid var(--line);background:linear-gradient(180deg,#f7f9fa,#e9eef1)}
.product-label{margin:0 10px;background:#e9ecee;border-bottom:4px solid var(--blue);text-align:center;font-family:'Raleway',sans-serif;font-size:13px;font-weight:600;padding:12px 0}
.map{position:absolute;top:1840px;left:0;width:1200px;height:320px;background:linear-gradient(135deg,#e6e4dc,#d8dbd0 50%,#e4e2da)}
.newsletter{position:absolute;top:2160px;left:0;width:1200px;height:152px;background:#2cb4e6}
.newsletter svg{position:absolute;left:0;top:0}
.newsletter h2{position:absolute;left:150px;top:46px;font-family:'Raleway',sans-serif;font-size:25px;font-weight:700;color:var(--white);line-height:32px;letter-spacing:.5px}
.nl-form{position:absolute;left:710px;top:34px;width:380px;color:var(--white);font-size:12px;line-height:18px}
.nl-form .field{margin-top:20px;display:flex}
.nl-form .input{width:240px;height:34px;background:var(--white);color:#9aa0a5;padding:8px 12px}
.nl-form .go{width:34px;height:34px;background:var(--bar)}
.footer{position:absolute;top:2312px;left:0;width:1200px;height:52px;background:var(--footer);color:#aab0b5;font-size:12px;display:flex;align-items:center;justify-content:space-between;padding:0 40px}
.footer .social span{background:#4d5257;width:24px;height:24px}
</style>
</head>
<body>
<div class="topbar"><span>Medical Guide Come to Expert the Best in Town</span><div class="social"><span></span><span></span><span></span></div></div>

<header class="header">
  <div class="brand">Harbourside Pharmacy</div>
  <nav class="nav"><a>Home</a><a class="active">About Us</a><a>Pages</a><a>Procedures</a><a>Gallery</a><a>Contact Us</a></nav>
</header>

<section class="hero">
  <div class="hero-photo" role="img" aria-label="Photo of a smiling pharmacist in a white coat beside scattered white tablets"></div>
  <div class="hero-text">
    <h1>PERSPICIATIS UNDE OMNIS</h1>
    <p>Sed ut perspiciatis unde omnis iste natus error sit voluptatem accusantium doloremque laudantium totam rem aperiam eaque ipsa quae ab illo inventore.</p>
    <span class="btn">READ MORE</span>
  </div>
</section>

<section class="features">
  <div class="feature">
    <svg viewBox="0 0 80 80"><path d="M30 8h20v22h22v20H50v22H30V50H8V30h22z" fill="none" stroke="#fff" stroke-width="4"/></svg>
    <div class="label">Individual Care</div><div class="plus">+</div>
  </div>
  <div class="feature mid">
    <svg viewBox="0 0 80 80"><path d="M12 36h56c0 16-12 26-28 26S12 52 12 36z" fill="#fff"/><rect x="30" y="62" width="20" height="6" fill="#fff"/><path d="M44 34L64 12" stroke="#fff" stroke-width="6" stroke-linecap="round"/></svg>
    <div class="label">What is Compounding?</div><div class="plus">+</div>
  </div>
  <div class="feature">
    <svg viewBox="0 0 80 80"><circle cx="40" cy="40" r="28" fill="#fff"/><circle cx="40" cy="40" r="14" fill="none" stroke="#27a4dc" stroke-width="4"/><path d="M40 30v20M30 40h20" stroke="#27a4dc" stroke-width="4"/></svg>
    <div class="label">Be Rewarded</div><div class="plus">+</div>
  </div>
</section>

<div class="section-title" style="top:910px"><span class="rule"></span><span class="dot"></span>WELCOME TO HARBOURSIDE PHARMACY<span class="dot"></span><span class="rule"></span></div>

<section class="info">
  <div class="info-item"><div class="info-icon"><svg width="30" height="30" viewBox="0 0 30 30"><rect x="4" y="8" width="10" height="18" rx="2" fill="#fff"/><rect x="16" y="8" width="10" height="18" rx="2" fill="#fff"/><rect x="5" y="4" width="8" height="4" fill="#fff"/><rect x="17" y="4" width="8" height="4" fill="#fff"/></svg></div>
    <div><h3>We do Compounding</h3><p>Sed ut perspiciatis unde omnis iste natus error sit voluptatem accusantium doloremque laudantium, totam rem aperiam, eaque ipsa quae ab illo inventore.</p></div></div>
  <div class="info-item"><div class="info-icon"><svg width="30" height="30" viewBox="0 0 30 30"><rect x="2" y="9" width="18" height="12" fill="#fff"/><path d="M20 12h5l3 4v5h-8z" fill="#fff"/><circle cx="8" cy="23" r="3" fill="#fff"/><circle cx="23" cy="23" r="3" fill="#fff"/></svg></div>
    <div><h3>Where we are</h3><p>Sed ut perspiciatis unde omnis iste natus error sit voluptatem accusantium doloremque laudantium, totam rem aperiam, eaque ipsa quae ab illo inventore.</p></div></div>
  <div class="info-item"><div class="info-icon"><svg width="30" height="30" viewBox="0 0 30 30"><circle cx="15" cy="15" r="11" fill="none" stroke="#fff" stroke-width="3"/><path d="M15 8v7l5 3" stroke="#fff" stroke-width="3" fill="none"/></svg></div>
    <div><h3>When we are there</h3><p>Sed ut perspiciatis unde omnis iste natus error sit voluptatem accusantium doloremque laudantium, totam rem aperiam, eaque ipsa quae ab illo inventore.</p></div></div>
  <div class="info-item"><div class="info-icon"><svg width="30" height="30" viewBox="0 0 30 30"><path d="M8 4l5 5-3 3c2 4 4 6 8 8l3-3 5 5-4 4C12 25 5 18 4 8z" fill="#fff"/></svg></div>
    <div><h3>How you can visit contact</h3><p>Sed ut perspiciatis unde omnis iste natus error sit voluptatem accusantium doloremque laudantium, totam rem aperiam, eaque ipsa quae ab illo inventore.</p></div></div>
</section>

<div class="section-title" style="top:1400px"><span class="rule"></span><span class="dot"></span>FEATURED PRODUCTS &amp; SERVICES<span class="dot"></span><span class="rule"></span></div>

<section class="products">
  <div class="product"><div class="product-img" role="img" aria-label="Product photo: boxed syrup and lozenges"></div><div class="product-label">PERSPICIATIS UNDE OMNIS</div></div>
  <div class="product"><div class="product-img" role="img" aria-label="Product photo: wrapped soap bar"></div><div class="product-label">PERSPICIATIS UNDE OMNIS</div></div>
  <div class="product"><div class="product-img" role="img" aria-label="Product photo: cold remedy packs"></div><div class="product-label">PERSPICIATIS UNDE OMNIS</div></div>
  <div class="product"><div class="product-img" role="img" aria-label="Product photo: skincare bottles and tubes"></div><div class="product-label">PERSPICIATIS UNDE OMNIS</div></div>
</section>

<div class="map" role="img" aria-label="Street map showing the pharmacy location"></div>

<section class="newsletter">
  <svg width="640" height="152" viewBox="0 0 640 152"><path d="M0 0H560L620 76 560 152H0z" fill="#1a8fc6"/></svg>
  <h2>SUBSCRIBE TO OUR<br>NEWSLETTER</h2>
  <div class="nl-form">
    <div>Lorem ipsum dolor sit amet consectetur adipiscing elit sed do eiusmod tempor</div>
    <div class="field"><span class="input">Enter Email</span><span class="go"></span></div>
  </div>
</section>

<footer class="footer"><span>© Copyright Harbourside Pharmacy. All Rights Reserved.</span><div class="social"><span></span><span></span><span></span><span></span></div></footer>
</body>
</html>
```